Im open to ideas.. I was thinking on my business cards aswell as my logo. a place for my name. email. phone number and abn..

ive attched a file with my business logo. which i dont love the colours.. i was think a dark background with charcoal letters so something along those colour schumes but im open to ideas..

BRM Constructions

```html
<!DOCTYPE html>
<html lang="en">
<head>
<meta charset="utf-8">
<title>BRM Constructions – Business Card</title>
<link href="https://fonts.googleapis.com/css2?family=Arimo:wght@400;700&display=swap" rel="stylesheet">
<style>
  :root {
    --backdrop: #8c8c8c;
    --card: #232323;
    --ink: #f2f2f2;
    --ink-soft: #d6d6d6;
  }
  html, body {
    margin: 0;
    padding: 0;
    width: 1200px;
    height: 844px;
    overflow: hidden;
    background: var(--backdrop);
  }
  .stage {
    width: 1200px;
    height: 844px;
    display: flex;
    align-items: center;
    justify-content: center;
  }
  .business-card {
    position: relative;
    width: 840px;
    height: 480px;
    background: var(--card);
    border-radius: 6px;
    font-family: "Arimo", Arial, sans-serif;
    color: var(--ink);
    box-sizing: border-box;
  }
  .contact {
    position: absolute;
    left: 64px;
    top: 60px;
  }
  .contact__name {
    margin: 0;
    font-size: 30px;
    font-weight: 700;
    letter-spacing: 1px;
  }
  .contact__role {
    margin: 6px 0 20px;
    font-size: 15px;
    font-weight: 400;
    letter-spacing: 1px;
    color: var(--ink-soft);
    text-transform: uppercase;
  }
  .contact__line {
    margin: 0 0 6px;
    font-size: 21px;
    font-weight: 400;
    color: var(--ink-soft);
  }
  .brand {
    position: absolute;
    right: 64px;
    bottom: 70px;
    display: flex;
    align-items: center;
    gap: 16px;
  }
  .brand__square {
    width: 26px;
    height: 26px;
    background: var(--ink);
  }
  .brand__name {
    font-size: 40px;
    font-weight: 700;
    letter-spacing: 2px;
    color: var(--ink);
    text-transform: uppercase;
  }
</style>
</head>
<body>
  <main class="stage">
    <article class="business-card">
      <section class="contact">
        <h1 class="contact__name">ALEX MORGAN</h1>
        <p class="contact__role">Construction Manager</p>
        <p class="contact__line">(555) 201-4830</p>
        <p class="contact__line">amorgan@brmconstructions.com</p>
        <p class="contact__line">ABN 9876543210</p>
      </section>
      <div class="brand">
        <span class="brand__square"></span>
        <span class="brand__name">BRM Constructions</span>
      </div>
    </article>
  </main>
</body>
</html>
```